WordPress Design for both website and landing page for an expert

I need a clean and stylish design for my new website. I work as an expert (see attached file WHY HOW WHAT), my product is expert opinion (reports) for company evaluations You can use all of the attached pictures colored or black / white. The person is me, you can add other pictures, if you want. The design should be clean and stylish, so you could use white, black, gray, silver and / or one additional color. I have added an idea about my website, see attached file CONCEPT WEBSITE If you have any more information, please do not hesitate to contact us 'Hesitate to ask me ...

```html
<!DOCTYPE html>
<html lang="de">
<head>
<meta charset="utf-8">
<title>Jonas Hartwig – Sachverständiger für Firmenbewertungen</title>
<link href="https://fonts.googleapis.com/css2?family=Roboto+Condensed:wght@400;700&family=Poppins:wght@400;500&family=Open+Sans:wght@400;600&display=swap" rel="stylesheet">
<style>
:root{
  --navy:#1f3f8f;
  --navy-dark:#12306e;
  --blue:#1d56a6;
  --teal:#2bab8c;
  --teal-dark:#1f8e74;
  --ink:#222;
  --grey:#555;
  --white:#fff;
  --silver:#8c8f95;
}
*{margin:0;padding:0;box-sizing:border-box}
html,body{width:1200px;height:3704px;overflow:hidden;background:var(--white)}
body{font-family:'Open Sans',sans-serif;color:var(--ink);position:relative}
h1,h2,h3{font-weight:400}
.abs{position:absolute}

/* header */
.site-header{position:absolute;left:0;top:0;width:1200px;height:150px;background:var(--white)}
.brand{position:absolute;left:78px;top:24px;width:280px;height:100px;display:flex;flex-direction:column;align-items:center;justify-content:center;gap:10px}
.brand-dot{flex-shrink:0;width:46px;height:46px;border-radius:50%;background:var(--silver);display:block}
.brand-name{font-family:'Poppins',sans-serif;font-size:25px;letter-spacing:3px;color:var(--silver);font-weight:400;white-space:nowrap}
.phone{position:absolute;left:752px;top:34px;font-size:18px;color:var(--ink);display:flex;align-items:center;gap:6px}
.search{position:absolute;left:926px;top:28px;width:184px;height:34px;border:2px solid var(--ink);border-radius:17px;font-size:13px;padding:7px 14px;color:#444}
.search svg{position:absolute;right:12px;top:8px}
.main-nav{position:absolute;left:450px;top:84px;display:flex;font-size:17px;white-space:nowrap}
.main-nav a{color:var(--ink);text-decoration:none;margin-right:38px}
.main-nav a.current{color:var(--blue)}

/* hero */
.hero{position:absolute;left:0;top:150px;width:1200px;height:670px;background:linear-gradient(100deg,#e9e9e7 0%,#d9d9d6 45%,#b7b6b2 70%,#9d9c98 100%)}
.hero-title{position:absolute;left:90px;top:128px;font-family:'Roboto Condensed',sans-serif;font-weight:700;color:var(--navy);line-height:1}
.hero-title .l1{font-size:78px;display:block}
.hero-title .l2{font-size:54px;display:block;margin-top:10px}
.hero-sub{position:absolute;left:90px;top:285px;font-family:'Roboto Condensed',sans-serif;font-size:33px;line-height:43px;color:#222}
.btn-outline{position:absolute;left:90px;top:398px;width:178px;height:50px;border:2px solid var(--navy);color:var(--navy);font-family:'Roboto Condensed',sans-serif;font-weight:700;font-size:20px;display:flex;align-items:center;justify-content:center}
.slider-dots{position:absolute;left:1158px;top:228px;display:flex;flex-direction:column;gap:12px}
.slider-dots i{width:8px;height:8px;border-radius:50%;background:#9aa7b8;display:block}
.slider-dots i.on{background:var(--blue)}

/* why */
.why-title{position:absolute;left:0;top:875px;width:1200px;text-align:center;font-family:'Poppins',sans-serif;font-weight:400;font-size:44px;color:#111}
.card{position:absolute;top:1052px;width:314px;height:320px;background:var(--white);border:1px solid #d8d8d8;box-shadow:0 2px 8px rgba(0,0,0,.18);text-align:center}
.card-icon{position:absolute;left:96px;top:-62px;width:122px;height:122px;border-radius:50%;background:var(--blue);display:flex;align-items:center;justify-content:center}
.card h3{margin-top:96px;font-family:'Poppins',sans-serif;font-weight:500;font-size:25px;color:#111}
.card p{margin:22px auto 0;width:262px;font-size:14px;line-height:25px;color:#333}
.card .more{position:absolute;left:0;bottom:30px;width:100%;color:var(--blue);font-size:16px}

/* faq */
.faq{position:absolute;left:0;top:1518px;width:1200px;height:497px;background:linear-gradient(120deg,var(--teal-dark),var(--teal) 60%,#37b898)}
.faq-notch{position:absolute;left:560px;top:1518px}
.laptop{position:absolute;left:0;top:80px;width:540px;height:370px;background:linear-gradient(180deg,#cfd3d8,#eef0f2 60%,#b9bdc2);border-radius:0 14px 6px 0}
.faq-title{position:absolute;left:570px;top:84px;font-family:'Poppins',sans-serif;font-weight:400;font-size:40px;color:var(--white)}
.faq-item{position:absolute;left:573px;width:539px;border:1.5px solid var(--white);color:var(--white);font-size:14px;line-height:19px;padding:0 50px 0 12px;display:flex;align-items:center}
.faq-item .plus{position:absolute;right:10px;top:50%;margin-top:-11px;width:22px;height:22px;border-radius:50%;background:var(--white);color:var(--teal);font-weight:700;font-size:20px;line-height:22px;text-align:center}

/* about */
.about-box{position:absolute;left:88px;top:2165px;width:552px;height:343px;border:2px solid var(--navy);background:var(--white)}
.about-box h2{position:absolute;left:42px;top:40px;font-family:'Poppins',sans-serif;font-weight:500;font-size:42px;color:#111}
.about-box p{position:absolute;left:42px;width:450px;font-size:15.5px;line-height:25px;color:#444}
.video{position:absolute;left:598px;top:2245px;width:514px;height:330px;background:linear-gradient(90deg,#d6dde2,#aab5bd 50%,#4c545b 75%,#c9d1d6);border:1px solid #bbb}
.play{position:absolute;left:222px;top:130px;width:70px;height:70px;border-radius:50%;background:rgba(255,255,255,.9);border:3px solid #222}

/* what we do */
.what{position:absolute;left:0;top:2700px;width:1200px;height:560px;background:linear-gradient(180deg,var(--navy-dark),#1a3f8a 60%,#1d4791)}
.what-title{position:absolute;left:0;top:110px;width:1200px;text-align:center;font-family:'Poppins',sans-serif;font-weight:400;font-size:44px;color:var(--white)}
.what-text{position:absolute;left:0;width:1200px;text-align:center;color:var(--white);font-size:19px;line-height:32px}
.btn-white{position:absolute;height:42px;border:2px solid var(--white);border-radius:8px;color:var(--white);font-size:19px;display:flex;align-items:center;justify-content:center}

/* footer */
.site-footer{position:absolute;left:0;top:3200px;width:1200px;height:504px;background:linear-gradient(180deg,#f4f6f9,#e3e8ef 70%,#dbe1ea)}
.foot-brand{position:absolute;left:0;top:150px;width:1200px;display:flex;flex-direction:column;align-items:center;gap:16px}
.foot-brand .brand-dot{width:80px;height:80px}
.foot-brand .brand-name{font-size:36px;letter-spacing:6px}
.foot-nav{position:absolute;left:0;top:308px;width:1200px;text-align:center;font-size:17px}
.foot-nav a{color:#222;text-decoration:none;margin:0 17px}
.social{position:absolute;left:472px;top:360px;display:flex;gap:14px}
.social span{width:40px;height:40px;border-radius:50%;border:2px solid #222;display:block}
.copyright{position:absolute;left:0;top:432px;width:1200px;text-align:center;font-size:13px;color:#333}
</style>
</head>
<body>

<header class="site-header">
  <div class="brand"><span class="brand-dot"></span><span class="brand-name">JONAS HARTWIG</span></div>
  <div class="phone">
    <svg width="16" height="16" viewBox="0 0 24 24"><path fill="#1d56a6" d="M6.6 10.8a15 15 0 0 0 6.6 6.6l2.2-2.2c.3-.3.7-.4 1-.2 1.1.4 2.3.6 3.6.6.6 0 1 .4 1 1V20c0 .6-.4 1-1 1A17 17 0 0 1 3 4c0-.6.4-1 1-1h3.5c.6 0 1 .4 1 1 0 1.3.2 2.5.6 3.6.1.3 0 .7-.2 1z"/></svg>
    1-800-555-0142
  </div>
  <div class="search">Search
    <svg width="14" height="14" viewBox="0 0 24 24"><circle cx="10" cy="10" r="7" fill="none" stroke="#222" stroke-width="3"/><path d="M15 15l6 6" stroke="#222" stroke-width="3"/></svg>
  </div>
  <nav class="main-nav">
    <a class="current" href="#">Home</a><a href="#">What I do</a><a href="#">Why I do it &amp; how I do it</a><a href="#">About me</a><a href="#" style="margin-right:0">Contact</a>
  </nav>
</header>

<section class="hero" role="img" aria-label="Portrait of the expert in a white shirt leaning on a railing in front of a concrete wall">
  <h1 class="hero-title"><span class="l1">Sachverständiger</span><span class="l2">für Firmenbewertungen</span></h1>
  <p class="hero-sub">Sie benötigen ein Gutachten zur Ermittlung<br>des Wertes Ihres Unternehmens</p>
  <div class="btn-outline">LEARN MORE</div>
  <div class="slider-dots"><i></i><i class="on"></i><i></i><i></i><i></i></div>
</section>
<svg class="abs" style="left:0;top:700px" width="1200" height="130" viewBox="0 0 1200 130">
  <polygon fill="#fff" points="0,20 55,16 185,46 380,62 500,70 590,118 700,68 830,64 1020,46 1160,16 1200,0 1200,130 0,130"/>
  <polyline fill="none" stroke="#9fb1c8" stroke-width="1.5" points="55,16 185,46 380,62 500,70 700,68 830,64 1020,46 1160,16"/>
  <g fill="#fff" stroke="#1d56a6" stroke-width="2">
    <circle cx="55" cy="16" r="4"/><circle cx="185" cy="46" r="4"/><circle cx="380" cy="62" r="4"/><circle cx="500" cy="70" r="4"/><circle cx="700" cy="68" r="4"/><circle cx="830" cy="64" r="4"/><circle cx="1020" cy="46" r="4"/><circle cx="1160" cy="16" r="4"/>
  </g>
</svg>

<h2 class="why-title">Why you should work with me</h2>

<article class="card" style="left:96px">
  <div class="card-icon"><svg width="60" height="60" viewBox="0 0 60 60" fill="none" stroke="#fff" stroke-width="5"><circle cx="24" cy="34" r="9"/><circle cx="24" cy="34" r="16" stroke-dasharray="6 4"/><circle cx="44" cy="20" r="5" stroke-width="4"/><circle cx="44" cy="20" r="10" stroke-width="4" stroke-dasharray="4 3"/></svg></div>
  <h3>Schnell</h3>
  <p>Sie bekommen Ihr Gutachten zeitnah (innerhalb von max. 21 Tagen nach Zugang aller benötigten Unterlagen)</p>
  <span class="more">Read More »</span>
</article>
<article class="card" style="left:440px">
  <div class="card-icon"><svg width="56" height="50" viewBox="0 0 56 50"><rect x="3" y="3" width="50" height="32" rx="3" fill="none" stroke="#fff" stroke-width="5"/><rect x="24" y="35" width="8" height="8" fill="#fff"/><rect x="14" y="43" width="28" height="5" fill="#fff"/></svg></div>
  <h3>Zertifiziert</h3>
  <p>Sie erhalten ein qualifiziertes und belastbares Gutachten von einem zertifizierten Sachverständigen (höchste Akzeptanz bei allen Parteien)</p>
  <span class="more">Read More »</span>
</article>
<article class="card" style="left:783px">
  <div class="card-icon"><svg width="58" height="50" viewBox="0 0 58 50" fill="#fff"><ellipse cx="22" cy="18" rx="20" ry="15"/><path d="M8 28 L4 40 L18 31z"/><ellipse cx="38" cy="30" rx="17" ry="12" stroke="#1d56a6" stroke-width="3"/><path d="M48 38 L54 47 L42 41z"/></svg></div>
  <h3>Verständlich</h3>
  <p>Ihr Gutachten wird für Sie logisch und nachvollziehbar sein und kein "Fachchinesisch" enthalten</p>
  <span class="more">Read More »</span>
</article>

<section class="faq">
  <div class="laptop" role="img" aria-label="Laptop screen showing business charts with a pen resting on a printed report"></div>
  <h2 class="faq-title">FAQ</h2>
  <div class="faq-item" style="top:154px;height:44px">Was sind die Kaufmotive der Kunden?<span class="plus">+</span></div>
  <div class="faq-item" style="top:208px;height:56px">Sie wollen Anteile Ihres Unternehmens oder Ihr gesamtes Unternehmen verkaufen?<span class="plus">+</span></div>
  <div class="faq-item" style="top:274px;height:56px">Sie wollen Ihr Unternehmen auf Ihre Erben übertragen und benötigen eine Bewertung für das Finanzamt?<span class="plus">+</span></div>
  <div class="faq-item" style="top:340px;height:58px">Sie müssen im Rahmen einer Trennung/Scheidung jemanden auszahlen und benötigen eine Bemessungsgrundlage?<span class="plus">+</span></div>
</section>
<svg class="faq-notch" width="80" height="22" viewBox="0 0 80 22"><polygon points="0,0 80,0 40,20" fill="#fff"/><polyline points="30,4 40,12 50,4" fill="none" stroke="#bbb" stroke-width="2"/></svg>

<section class="about-box">
  <h2>About me</h2>
  <p style="top:105px">Lassen Sie Ihr Unternehmen von einem qualifizierten Sachverständigen bewerten und gehen somit vielen (unnötigen) Streitereien aus dem Weg.</p>
  <p style="top:190px">Merke: Die Kosten für ein Gutachten sind immer überproportional günstiger als die Kosten für Rechtsstreitigkeiten. Und das losgelöst von der psychischen Belastung einer solchen Auseinandersetzung …</p>
</section>
<div class="video" role="img" aria-label="Video still of the expert in a dark suit standing in a bright office corridor">
  <div class="play"><svg width="64" height="64" viewBox="0 0 64 64"><polygon points="26,19 46,32 26,45" fill="#222"/></svg></div>
</div>

<section class="what">
  <h2 class="what-title">What We Do</h2>
  <p class="what-text" style="top:208px">My quality promise: should the advised date for the preparation of the report be<br>exceeded, you will receive the report free of chare</p>
  <div class="btn-white" style="left:514px;top:282px;width:172px">I waive my fee</div>
  <p class="what-text" style="top:350px">Mein Qualitätsversprechen: Sollte der avisierte Termin für die Erstellung des<br>Gutachtens überschritten werden, erhalten Sie das Gutachten absolut kostenfrei!</p>
  <div class="btn-white" style="left:440px;top:430px;width:320px">Ich verzichte auf mein Honorar</div>
</section>
<svg class="abs" style="left:560px;top:2700px" width="80" height="22" viewBox="0 0 80 22"><polygon points="0,0 80,0 40,20" fill="#fff"/><polyline points="30,4 40,12 50,4" fill="none" stroke="#bbb" stroke-width="2"/></svg>

<footer class="site-footer" role="img" aria-label="Faint city skyline behind the footer">
  <svg class="abs" style="left:0;top:0" width="1200" height="70" viewBox="0 0 1200 70"><polygon fill="#1d4791" points="0,0 1200,0 1200,70 1110,32 1010,22 900,48 720,36 610,58 500,40 410,56 280,30 120,12 60,30 0,22"/></svg>
  <div class="foot-brand"><span class="brand-dot"></span><span class="brand-name">JONAS HARTWIG</span></div>
  <nav class="foot-nav"><a href="#">Home</a><a href="#">What I do</a><a href="#">Why I do it &amp; how I do it</a><a href="#">About me</a><a href="#">Contact us</a></nav>
  <div class="social"><span></span><span></span><span></span><span></span><span></span></div>
  <p class="copyright">Copyright © 2018 All Rights Reserved</p>
</footer>

</body>
</html>
```